CD Cover for collection of relaxation music called "Under Quiet Willows"

We'd like to design a CD cover for upload to Brivola Press on Request and to digital services like Zelorn. The template and size specs, photos, example font and text are attached. We need the song durations on the back cover as well and we expect to have those ready by Thursday. Other album and book covers are provided for use as thumbnails inside booklet next to titles. In addition to the finished images to the template specifications, we'd like a copy of the front cover and the back cover as square images to upload to digital services - 2500 dpi x 2500 dpi or larger in .png and .jpg formats. We will also need to add "For more information, visit CalmingToneHaven.example" under the other available works list. Thanks and we look forward to working together.

Target Market(s)

Relaxation and meditation music. Yoga studios. Massage therapists. Reiki practitioners.

Industry/Entity Type

Music Download

Colors

Designer to choose colors to be used in the design.

Requirements
Must have
• Font consistent with previous works and a peaceful and attractive layout. Also, designers have discretion on which water images to use in which location. The goal is to have a cover image that stands out among other thumbnails in the stores and also for the images on the CD to tell a story of increasing peace and relaxation.

```html
<!DOCTYPE html>
<html lang="en">
<head>
<meta charset="utf-8">
<title>Under Quiet Willows – CD Booklet Panels</title>
<link rel="stylesheet" href="https://fonts.googleapis.com/css2?family=Gabriela&family=Italianno&display=swap">
<style>
  :root {
    --canvas: #000000;
    --ink-brown: #3a2a18;
    --ink-maroon: #5e1424;
    --gold: #f0c95a;
    --gold-deep: #c48f1e;
    --cream: #fbf1d2;
  }
  html, body {
    margin: 0;
    padding: 0;
    width: 1200px;
    height: 1200px;
    overflow: hidden;
    background: var(--canvas);
  }
  .sheet { position: relative; width: 1200px; height: 1200px; }
  .panel { position: absolute; overflow: hidden; }
  .panel--story   { left: 6px;   top: 6px;   width: 596px; height: 584px; }
  .panel--front   { left: 604px; top: 6px;   width: 592px; height: 584px; }
  .panel--works   { left: 6px;   top: 610px; width: 596px; height: 584px; }
  .panel--thanks  { left: 604px; top: 610px; width: 592px; height: 584px; }
  .photo { position: absolute; inset: 0; }
  .photo--yoga {
    background:
      radial-gradient(ellipse 60px 260px at 300px 340px, rgba(250,238,190,.85), rgba(250,238,190,0) 100%),
      linear-gradient(180deg, #3f8a8e 0%, #8fb7aa 18%, #e6dcae 34%, #f4e7b8 40%, #1d2a22 46%, #1b2a24 52%, #5f7f82 60%, #8aa7ad 75%, #4b6468 100%);
  }
  .photo--loons {
    background:
      linear-gradient(180deg, #f2a310 0%, #2a1a05 9%, #0a0804 22%, #0a0804 44%, #ffd21a 49%, #f3b60c 52%, #1a1204 56%, #5a3d06 64%, #f6c414 76%, #f3b10e 100%);
  }
  .photo--paddle {
    background:
      radial-gradient(circle 70px at 316px 430px, rgba(255,240,200,.9), rgba(255,240,200,0) 100%),
      linear-gradient(180deg, #7f7fa8 0%, #b8bfd0 25%, #d6d3c4 52%, #2b2a22 61%, #2b2a22 66%, #b8b3a3 70%, #6f6e80 85%, #3e3d55 100%);
  }
  .photo--pines {
    background:
      radial-gradient(ellipse 180px 240px at 300px 380px, rgba(255,250,240,.85), rgba(255,250,240,0) 100%),
      linear-gradient(90deg, rgba(20,16,20,.9) 0%, rgba(20,16,20,0) 18%, rgba(20,16,20,0) 80%, rgba(20,16,20,.85) 100%),
      linear-gradient(180deg, #c9bde0 0%, #e6dbe8 40%, #8c8596 60%, #c7a9c9 82%, #3a3038 100%);
  }
  .copy {
    position: absolute;
    left: 0; right: 0;
    margin: 0;
    text-align: center;
    font-family: "Gabriela", serif;
    font-size: 12.6px;
    line-height: 20.8px;
  }
  .copy--story { top: 38px; color: var(--ink-brown); }
  .copy--works { top: 72px; color: var(--ink-maroon); line-height: 20.8px; }
  .copy--works p { margin: 0 0 20.8px; }
  .copy--thanks { top: 156px; left: 150px; right: 150px; color: var(--ink-maroon); }
  .copy--thanks p { margin: 0 0 20.8px; }
  .cover-title {
    position: absolute;
    left: 0; right: 0;
    margin: 0;
    text-align: center;
    font-family: "Italianno", cursive;
    color: var(--gold);
    font-weight: 400;
    line-height: 1;
  }
  .cover-title--main { top: 88px; font-size: 70px; }
  .cover-title--sub  { top: 172px; font-size: 42px; color: var(--cream); line-height: 52px; }
  .cover-title--artist { top: 338px; font-size: 44px; color: var(--cream); }
</style>
</head>
<body>
<main class="sheet">
  <section class="panel panel--story">
    <div class="photo photo--yoga" role="img" aria-label="Woman in a tree yoga pose on a dock at a sunlit lake, arms raised"></div>
    <p class="copy copy--story">
      Water has always been a comfort in my life. Growing up, extended walks along the banks of<br>
      the Alder Bend River were among my favorite retreats. Sometimes, the water was my burbling<br>
      and swirling companion. Other times, when problems were on my mind, I’d pick up a stone,<br>
      whisper my troubles into it and then throw the stone into the water to be cleansed.<br>
      Today, water steadies me. Warm baths are healing waters and swimming is a baptism.<br>
      This collection of music has been developed to support you in restoring feelings of peace and<br>
      tranquility. These songs have found a home in local yoga classes and in meditative concerts.
    </p>
  </section>

  <section class="panel panel--front">
    <div class="photo photo--loons" role="img" aria-label="Golden sunset over a lake with silhouetted pines and two loons on the water"></div>
    <h1 class="cover-title cover-title--main">Under Quiet Willows</h1>
    <p class="cover-title cover-title--sub">Healing Music for<br>Body, Mind and Spirit</p>
    <p class="cover-title cover-title--artist">by Lena Marsh-Corwin</p>
  </section>

  <section class="panel panel--works">
    <div class="photo photo--paddle" role="img" aria-label="Woman on a paddleboard on a calm lake at sunset"></div>
    <div class="copy copy--works">
      <p>To find more of my work, search for these titles on<br>Zelorn, Brivola, Quenly and other leading outlets.</p>
      <p>Starlit Cradle Songs - For those who have lost a child.</p>
      <p>Hush and Rest - 33 Lullabies for Babies</p>
    </div>
  </section>

  <section class="panel panel--thanks">
    <div class="photo photo--pines" role="img" aria-label="Tall pine trunks framing a lake under a soft lavender sky"></div>
    <div class="copy copy--thanks">
      <p>Special Thanks:<br>
      To my parents who encourage my journey. To Miriam and Corinne of Lotus Tide Yoga and Wellness who have opened new doors for me and in me. To Rowan Ashby for his calm in the studio and his editing expertise. To all the wonderful people who sent me emails over the years telling me that my music touched their lives in some way. Your notes have inspired me. And to my husband, Owen, who has always supported my voice and bringing it to the world. You are a light on my path.</p>
      <p>Your arms are my safe harbor.</p>
    </div>
  </section>
</main>
</body>
</html>
```